Salon and Spa Distributor Business Card

Need a business card. We are are distributor in the salon and spa industry. We identify with natural beauty. Need a card with:
Company Name: Petal Quarry"
Title: "President & CEO"
Address
Company Phone number
email
website
Tag Line:" The Professional Salon Source"

Industry/Entity Type

Business

Contact Information for Business Card

Name: Dov Strommen
Title: "President & CEO"
Address: 31 Harlow Ln, Bexmoor, NJ 07813
Company Phone number: 800-463-5918
email: dovstrommen@petalquarry.example
website: www.petalquarry.example

Requirements
Should not have
• No black backgrounds

```html
<!DOCTYPE html>
<html lang="en">
<head>
<meta charset="utf-8">
<title>Petal Quarry Business Card</title>
<link rel="stylesheet" href="https://fonts.googleapis.com/css2?family=Open+Sans:wdth,wght@75..100,300..800&display=swap">
<style>
  :root {
    --backdrop: #000000;
    --card-paper: #f3f3f3;
    --brand-green: #3fa535;
    --brand-green-light: #5bbb45;
    --leaf-deep: #1f7a3a;
    --leaf-bright: #6cc04a;
    --ink: #2b2b2b;
    --white: #ffffff;
  }
  * { margin: 0; padding: 0; box-sizing: border-box; }
  html, body {
    width: 1200px; height: 900px; overflow: hidden;
    background: var(--backdrop);
    font-family: "Open Sans", sans-serif;
  }
  .stage { position: relative; width: 1200px; height: 900px; }

  .card-front {
    position: absolute; left: 265px; top: 200px;
    width: 310px; height: 502px;
    background: var(--card-paper);
    border-radius: 52px 0 52px 0;
    color: var(--ink);
  }
  .brand {
    position: absolute; left: 30px; top: 92px;
    display: flex; align-items: center; gap: 12px;
  }
  .brand-dot {
    width: 26px; height: 26px; border-radius: 50%;
    background: var(--brand-green);
  }
  .brand-name {
    font-size: 24px; font-weight: 400; color: var(--brand-green);
    letter-spacing: -0.2px; font-stretch: 92%;
  }
  .person { position: absolute; left: 23px; top: 296px; }
  .person-name {
    font-size: 18px; font-weight: 700; color: var(--brand-green);
    font-stretch: 90%; line-height: 1.2;
  }
  .person-title { font-size: 13px; line-height: 1.4; font-stretch: 90%; }
  .address {
    position: absolute; left: 24px; top: 355px;
    font-size: 13px; line-height: 21px; font-stretch: 90%;
  }
  .contacts {
    position: absolute; left: 24px; top: 417px;
    list-style: none; font-size: 13px; line-height: 20.5px; font-stretch: 90%;
  }
  .contacts li { display: flex; align-items: center; gap: 8px; }
  .contacts svg { width: 11px; height: 11px; fill: var(--brand-green); flex: none; }

  .card-back {
    position: absolute; left: 641px; top: 200px;
    width: 309px; height: 502px;
    border-radius: 0 52px 0 52px;
    overflow: hidden;
  }
  .leaf-artwork {
    position: absolute; inset: 0;
    background:
      radial-gradient(ellipse at 20% 15%, var(--leaf-bright) 0%, transparent 45%),
      radial-gradient(ellipse at 85% 55%, var(--leaf-deep) 0%, transparent 50%),
      linear-gradient(160deg, var(--brand-green) 0%, var(--leaf-bright) 55%, var(--brand-green) 100%);
  }
  .tagline { position: absolute; inset: 0; }
  .tagline text { fill: var(--white); font-family: "Open Sans", sans-serif; font-weight: 600; font-stretch: 88%; }
</style>
</head>
<body>
<main class="stage">
  <section class="card-front" aria-label="Business card front">
    <div class="brand">
      <span class="brand-dot"></span>
      <span class="brand-name">Petal Quarry</span>
    </div>
    <div class="person">
      <p class="person-name">Dov Strommen</p>
      <p class="person-title">President &amp; CEO</p>
    </div>
    <address class="address" style="font-style:normal">
      31 Harlow Ln,<br>Bexmoor, NJ 07813
    </address>
    <ul class="contacts">
      <li><svg viewBox="0 0 24 24"><path d="M6.6 10.8a15 15 0 0 0 6.6 6.6l2.2-2.2a1 1 0 0 1 1-.25 11.4 11.4 0 0 0 3.6.57 1 1 0 0 1 1 1V20a1 1 0 0 1-1 1A17 17 0 0 1 3 4a1 1 0 0 1 1-1h3.5a1 1 0 0 1 1 1c0 1.25.2 2.45.57 3.6a1 1 0 0 1-.25 1z"/></svg>800-463-5918</li>
      <li><svg viewBox="0 0 24 24"><path d="M2 5h20v14H2z M2 5l10 8 10-8" /></svg>dovstrommen@petalquarry.example</li>
      <li><svg viewBox="0 0 24 24"><circle cx="12" cy="12" r="10"/></svg>www.petalquarry.example</li>
    </ul>
  </section>

  <section class="card-back" aria-label="Business card back">
    <div class="leaf-artwork" role="img" aria-label="Green leaf and flowing hair artwork"></div>
    <svg class="tagline" viewBox="0 0 309 502" aria-label="The Professional Salon Source">
      <text x="29" y="192" font-size="118" textLength="238" lengthAdjust="spacingAndGlyphs">THE</text>
      <text x="31" y="240" font-size="35" textLength="244" lengthAdjust="spacingAndGlyphs">PROFESSIONAL</text>
      <text x="31" y="322" font-size="73" textLength="240" lengthAdjust="spacingAndGlyphs">SALON</text>
      <text x="31" y="395" font-size="71" textLength="253" lengthAdjust="spacingAndGlyphs">SOURCE</text>
    </svg>
  </section>
</main>
</body>
</html>
```